Need a business card design for a residential architect.

You can get a sense of his work at www.tberlove.com

Would like a consistent look and feel between business card and website
.

Target Market(s)

Residential homeowners builders

Industry/Entity Type

Residential

Contact Information for Business Card

Dale Morrick
Principle
Morrick Architecture
418 Kestrel Lane
Menlo Park, CA 94025

dale@tberlove.com

tberlove.com
phone: 650-555-2716
Fax: 650-555-8043

Font styles to use
Sans Serif

Requirements
Must have
• Details above
Nice to have
• Would like a consistent look and feel between business card and website
Should not have
• None

```html
<!DOCTYPE html>
<html lang="en">
<head>
<meta charset="utf-8">
<title>Morrick Architecture – Business Card</title>
<link rel="stylesheet" href="https://fonts.googleapis.com/css2?family=Exo+2:wght@400;600&display=swap">
<style>
  :root {
    --backdrop: #e9e7e3;
    --card: #ffffff;
    --ink: #3a3a3a;
    --ink-soft: #5c5c5c;
    --band: #8c8c8c;
    --band-light: #a9a9a9;
    --on-band: #f4f4f4;
  }
  * { box-sizing: border-box; margin: 0; padding: 0; }
  html, body { width: 1200px; height: 828px; overflow: hidden; }
  body {
    background: var(--backdrop);
    font-family: "Exo 2", sans-serif;
    color: var(--ink);
    position: relative;
  }
  .card {
    position: absolute;
    top: 259px;
    width: 540px;
    height: 310px;
    background: var(--card);
    box-shadow: 0 6px 22px rgba(0,0,0,.12);
    overflow: hidden;
  }
  .card--front { left: 40px; }
  .card--back { left: 620px; }

  .wordmark { text-align: center; font-weight: 600; color: var(--ink-soft); line-height: 1; }
  .wordmark__name { display: block; font-size: 46px; letter-spacing: 1px; }
  .wordmark__sub { display: block; font-size: 15px; letter-spacing: 9px; margin-top: 4px; }
  .card--front .wordmark { position: absolute; left: 0; right: 0; top: 112px; }

  .card--back .wordmark { position: absolute; left: 26px; top: 26px; text-align: left; }
  .card--back .wordmark__name { font-size: 34px; }
  .card--back .wordmark__sub { font-size: 11px; letter-spacing: 6.5px; }

  .name-band {
    position: absolute; left: 0; top: 104px; width: 210px; height: 36px;
    background: var(--band); color: var(--on-band); padding: 4px 0 0 26px;
  }
  .name-band__name { font-size: 12px; letter-spacing: 1px; display: block; }
  .name-band__title { font-size: 8px; display: block; margin-top: 1px; }
  .band-stripes { position: absolute; left: 214px; top: 104px; }
  .band-rule { position: absolute; left: 0; right: 0; top: 136px; height: 4px; background: var(--band); }

  .contact { position: absolute; list-style: none; font-size: 12.5px; letter-spacing: .6px; color: var(--ink); }
  .contact li { display: flex; align-items: flex-start; gap: 8px; margin-bottom: 6px; }
  .contact svg { flex: none; margin-top: 2px; }
  .contact--main { left: 26px; top: 158px; }
  .contact--web { left: 290px; top: 232px; }

  .social { position: absolute; right: 0; top: 28px; list-style: none; font-size: 12.5px; letter-spacing: .4px; }
  .social li { display: flex; align-items: center; justify-content: flex-end; height: 26px; margin-bottom: 4px; }
  .social__dot { width: 20px; height: 20px; border-radius: 50%; background: var(--ink); margin-left: 8px; }
  .social__tail { width: 22px; height: 2px; background: var(--ink); }
</style>
</head>
<body>

<section class="card card--front" aria-label="Card front">
  <div class="wordmark">
    <span class="wordmark__name">MORRICK</span>
    <span class="wordmark__sub">ARCHITECTURE</span>
  </div>
</section>

<section class="card card--back" aria-label="Card back">
  <div class="wordmark">
    <span class="wordmark__name">MORRICK</span>
    <span class="wordmark__sub">ARCHITECTURE</span>
  </div>

  <div class="name-band">
    <span class="name-band__name">DALE MORRICK</span>
    <span class="name-band__title">Principal</span>
  </div>
  <svg class="band-stripes" width="80" height="34" viewBox="0 0 80 34" aria-hidden="true">
    <g fill="var(--band-light)">
      <polygon points="0,0 9,0 19,34 10,34"/>
      <polygon points="16,0 25,0 35,34 26,34"/>
      <polygon points="32,0 41,0 51,34 42,34"/>
      <polygon points="48,0 57,0 67,34 58,34"/>
    </g>
  </svg>
  <div class="band-rule"></div>

  <ul class="social">
    <li>linkfeed.com/morrick<span class="social__dot"></span><span class="social__tail"></span></li>
    <li>@chirper<span class="social__dot"></span><span class="social__tail"></span></li>
    <li>Callspace<span class="social__dot"></span><span class="social__tail"></span></li>
  </ul>

  <ul class="contact contact--main">
    <li>
      <svg width="13" height="13" viewBox="0 0 14 14" aria-hidden="true"><circle cx="7" cy="7" r="7" fill="var(--ink)"/><path d="M4.5 3.5l1.6 0 .6 2-1 .8a5 5 0 0 0 2.4 2.4l.8-1 2 .6 0 1.6c-3.6.4-6.8-2.8-6.4-6.4z" fill="#fff"/></svg>
      650-555-2716
    </li>
    <li>
      <svg width="13" height="13" viewBox="0 0 14 14" aria-hidden="true"><circle cx="7" cy="7" r="7" fill="var(--ink)"/><rect x="4" y="5" width="6" height="5" fill="#fff"/><rect x="5" y="3" width="4" height="2" fill="#fff"/></svg>
      650-555-8043
    </li>
    <li>
      <svg width="13" height="13" viewBox="0 0 14 14" aria-hidden="true"><circle cx="7" cy="7" r="7" fill="var(--ink)"/><path d="M7 3a2.6 2.6 0 0 1 2.6 2.6C9.6 7.6 7 11 7 11S4.4 7.6 4.4 5.6A2.6 2.6 0 0 1 7 3z" fill="#fff"/><circle cx="7" cy="5.6" r="1" fill="var(--ink)"/></svg>
      <span>418 Kestrel Lane<br>Menlo Park, CA 94025</span>
    </li>
  </ul>

  <ul class="contact contact--web">
    <li>
      <svg width="13" height="13" viewBox="0 0 14 14" aria-hidden="true"><circle cx="7" cy="7" r="7" fill="var(--ink)"/><rect x="3.5" y="4.5" width="7" height="5" fill="#fff"/><path d="M3.5 4.5L7 7.5l3.5-3" stroke="var(--ink)" stroke-width=".8" fill="none"/></svg>
      dale@tberlove.com
    </li>
    <li>
      <svg width="13" height="13" viewBox="0 0 14 14" aria-hidden="true"><circle cx="7" cy="7" r="6.3" fill="none" stroke="var(--ink)" stroke-width="1.2"/><ellipse cx="7" cy="7" rx="2.6" ry="6.3" fill="none" stroke="var(--ink)" stroke-width=".9"/><path d="M1 7h12M2 4.2h10M2 9.8h10" stroke="var(--ink)" stroke-width=".8"/></svg>
      www.tberlove.com
    </li>
  </ul>
</section>

</body>
</html>
```